AI Business Tools Landing Page

My web-based website builder (Pavlora.com) will be adding many new features in the very near future and I need an eye-catching landing page to promote these new products.

The page will have a primary section of the 8 main products we are promoting:
1. AI Instant Website Generator
2. AI Chatbot
3. Online Store Builder with AI Assistance
4. AI Auto-Blogging System
5. Online Scheduling System
6. Custom Email System
7. SEO Service
8. CRM System

The page will also have a smaller section for links to our affiliate programs. These can be smaller, less-promanent buttons or links. These are the affiliate products:
1. Get Your LLC
2. Website Design and Maintenance
3. Search Ads Management
4. Social Media Posting Service
5. Logo Design
6. Trademark Registration
7. Patent Application
8. Printing Services (including postcards, flyers, and merch.)
9. Bulk AI Content Generator

The theme and color scheme of the page should follow the theme of our main website, which is https://pavlora.com.

I need the page fully coded and ready to deploy on my server.

I look forward to seeing your amazing designs!

```html
<!DOCTYPE html>
<html lang="en">
<head>
<meta charset="utf-8">
<title>Pavlora – Mobile Preview</title>
<link href="https://fonts.googleapis.com/css2?family=Roboto:wght@300;400;500&display=swap" rel="stylesheet">
<style>
:root{
  --board:#0c3a86;
  --board-deep:#0a2d6a;
  --navy:#0d2a57;
  --navy-2:#103366;
  --ice:#eef5fc;
  --white:#ffffff;
  --ink:#1d2b3f;
  --muted:#5d6b80;
  --accent:#1ba6e8;
  --btn:#1b74dc;
  --btn-light:#36b8ee;
  --star:#f4b400;
}
*{box-sizing:border-box;margin:0;padding:0}
html,body{width:1200px;height:750px;overflow:hidden}
body{font-family:"Roboto",sans-serif;background:linear-gradient(90deg,var(--board-deep),var(--board) 60%,#0e4aa6);position:relative;color:var(--ink)}
.abs{position:absolute}
.accent{color:var(--accent)}
.tiny{font-size:5.5px;line-height:1.4;color:var(--muted)}
.tag{position:absolute;border:1px solid var(--accent);color:var(--accent);font-size:5px;padding:2px 5px;text-align:center}
.btn{position:absolute;background:var(--btn);color:#fff;font-size:6px;display:flex;align-items:center;justify-content:center;border-radius:2px}
.h{font-weight:300;line-height:1.18}
.media{position:absolute;border-radius:4px}

/* brand */
.brand{position:absolute;display:flex;align-items:center;gap:8px;color:#fff;font-weight:500}
.brand .dot{border-radius:50%;background:var(--accent)}

/* columns */
.col{position:absolute;top:0;height:750px;overflow:hidden}
.col-2{left:268px;width:157px;background:var(--white)}
.col-3{left:453px;width:157px;background:var(--ice)}
.col-4{left:640px;width:158px;background:var(--ice)}
.col-5{left:825px;width:158px;background:var(--ice)}
.col-6{left:1012px;width:158px;background:var(--navy)}

.card{position:absolute;left:22px;width:113px;background:#fff;border-radius:4px;box-shadow:0 2px 6px rgba(20,60,120,.12);text-align:center}
.card .ico{width:22px;height:22px;border:1px solid var(--accent);border-radius:50%;margin:12px auto 8px}
.card h4{font-weight:400;font-size:7.5px;color:var(--accent);line-height:1.25;padding:0 10px}
.card ul{list-style:none;text-align:left;padding:6px 12px 0}
.card li{font-size:3.8px;color:var(--muted);line-height:1.35;margin-bottom:4px;padding-left:4px;position:relative}
.card li::before{content:"";position:absolute;left:0;top:1.5px;width:1.6px;height:1.6px;border-radius:50%;background:var(--btn)}
.card .btn{position:relative;width:52px;height:12px;margin:6px auto 0;font-size:4.5px}

.review{position:absolute;left:20px;width:123px;height:92px;background:#fff;border-radius:3px;box-shadow:0 2px 6px rgba(20,60,120,.1);padding:10px 10px}
.stars{color:var(--star);font-size:6px;letter-spacing:1px}
.stars span{color:var(--ink);font-size:4.5px;letter-spacing:0}
.review p{font-size:4.6px;font-style:italic;color:var(--ink);line-height:1.4;margin-top:6px}
.who{display:flex;align-items:center;gap:5px;position:absolute;left:10px;bottom:10px}
.who i{width:12px;height:12px;border-radius:50%;background:#8a6b55;display:block}
.who b{font-size:4.8px;font-weight:500;display:block}
.who small{font-size:3.4px;color:var(--muted)}

.chip{position:absolute;background:var(--navy);color:#fff;font-size:3.4px;padding:2px 5px 2px 9px;border-radius:6px;white-space:nowrap}
.chip::before{content:"";position:absolute;left:2px;top:2px;width:5px;height:5px;border-radius:50%;background:var(--btn-light)}

.foot h5{position:absolute;left:32px;font-weight:400;font-size:8px;color:#fff}
.foot h5::after{content:"";position:absolute;left:0;top:15px;width:24px;height:1px;background:#fff}
.foot a{position:absolute;left:34px;font-size:6.5px;color:#dbe6f5;text-decoration:none}
</style>
</head>
<body>

<!-- intro -->
<div class="brand" style="left:58px;top:62px;font-size:25px">
  <span class="dot" style="width:36px;height:36px"></span>Pavlora
</div>
<div class="abs h" style="left:60px;top:114px;font-size:21px;color:#fff;font-weight:400">Preview Mobile</div>
<div class="abs" style="left:60px;top:139px;width:144px;text-align:right;font-size:13px;color:#fff">Version</div>

<!-- mobile home screen -->
<section class="abs" style="left:80px;top:190px;width:161px;height:560px;background:linear-gradient(180deg,var(--navy-2),var(--navy));overflow:hidden">
  <div class="brand" style="left:14px;top:16px;font-size:8.5px;gap:4px"><span class="dot" style="width:13px;height:13px"></span>Pavlora</div>
  <svg class="abs" style="left:133px;top:20px" width="10" height="8" viewBox="0 0 10 8"><path d="M0 1h10M0 4h10M0 7h10" stroke="#fff" stroke-width="1"/></svg>
  <div class="abs h" style="left:20px;top:67px;font-size:12.5px;color:#fff;font-weight:400">Create a<br><span style="background:var(--accent);padding:0 2px">Professional</span><br>Website for <span class="accent">your</span><br><span class="accent">Business</span> Now</div>
  <p class="abs" style="left:20px;top:144px;width:104px;font-size:5.6px;line-height:1.3;color:#dce7f7">Create your free website, change your website to make it look professional in order to make your business more popular with more people</p>
  <div class="abs" style="left:26px;top:211px;width:98px;height:20px;background:#fff;border-radius:2px;font-size:4.5px;color:#8a96a8;padding:7px 10px">Enter your business name</div>
  <div class="btn" style="left:44px;top:240px;width:56px;height:13px;font-size:4.5px">Build free Website</div>
  <div class="media" role="img" aria-label="Robot head split into glowing tiles" style="left:16px;top:286px;width:130px;height:155px;background:linear-gradient(135deg,#1c6b86,#0e3f5e 60%,#0a2a4a)"></div>
  <div class="abs" style="left:7px;top:475px;width:146px;height:70px;background:#0a2148;border-radius:5px;color:#fff;font-size:10px">
    <span class="abs" style="left:14px;top:14px;display:flex;align-items:center;gap:3px"><i style="width:10px;height:10px;background:#fff;display:block"></i>Northwind</span>
    <span class="abs" style="left:90px;top:14px">Corvexa</span>
    <span class="abs" style="left:18px;top:42px">Tallora</span>
    <span class="abs" style="left:86px;top:42px">Brimleaf</span>
  </div>
</section>

<!-- about -->
<section class="col col-2">
  <div class="tag" style="left:14px;top:29px;width:120px;font-size:3.8px">Discover the Future of Website Creation with Pavlora</div>
  <div class="abs" style="left:416px;top:45px;width:10px;height:36px;background:var(--accent)"></div>
  <h2 class="abs h" style="left:12px;top:64px;font-size:12.5px">Your <span class="accent">FREE</span> Stunn ing Website <span class="accent">In 1-Click Built</span> by Artificial Intelligence.</h2>
  <p class="abs tiny" style="left:12px;top:162px;width:106px;font-size:5.6px;line-height:1.35">In the rapidly evolving digital era, the integration of Artificial Intelligence (AI) into various sectors is unmistakably transformative. Website creation, a domain once dominated by manual coding and design intricacies, is now witnessing a groundbreaking revolution, thanks to AI technology. Enter Pavlora, a frontrunner in this innovative wave, offering an AI Website Builder that is redefining the paradigms of website development. With Pavlora, creativity knows no bounds, and building dynamic, responsive websites has become a matter of a few clicks.</p>
  <div class="btn" style="left:14px;top:328px;width:64px;height:17px;font-size:4.8px">Build Free Website</div>
  <div class="media" role="img" aria-label="Blue humanoid robot touching holographic screens" style="left:16px;top:383px;width:124px;height:182px;background:linear-gradient(160deg,#13305c,#1e5aa8 55%,#0c2148)"></div>
  <div class="abs" style="left:100px;top:381px;width:42px;height:42px;background:var(--btn-light);border:3px solid #fff;border-radius:5px;color:#fff;text-align:center">
    <div style="font-size:15px;font-weight:300;margin-top:4px">15<sup style="font-size:6px">+</sup></div>
    <div style="font-size:3.4px;line-height:1.1">YEARS OF EXPERIENCE</div>
  </div>
  <div class="abs" style="left:14px;top:538px;width:42px;height:27px;background:#9fdcf3;border:2px solid #fff;border-radius:5px;color:#1469a0;text-align:center">
    <div style="font-size:11px;font-weight:300;margin-top:1px">9k<sup style="font-size:5px">+</sup></div>
    <div style="font-size:3.2px">CLIENT ORDER</div>
  </div>
  <div class="abs" style="left:0;top:606px;width:157px;height:144px;background:var(--ice)"></div>
  <div class="tag" style="left:60px;top:632px;width:38px;font-size:3.8px">Our Feature</div>
  <h2 class="abs h" style="left:8px;top:660px;width:142px;text-align:center;font-size:12.5px">New <span class="accent">features</span> that are no less cool that you have to try</h2>
  <p class="abs tiny" style="left:6px;top:726px;width:146px;text-align:center;font-size:5.4px">The new features are more sophisticated than the previous features and contain many advanced technologies in processing</p>
</section>

<!-- features -->
<section class="col col-3">
  <div class="tag" style="left:60px;top:28px;width:38px;font-size:3.8px">Our Feature</div>
  <div class="abs" style="left:0;top:47px;width:10px;height:14px;background:#d6ebfa"></div>
  <h2 class="abs h" style="left:8px;top:57px;width:142px;text-align:center;font-size:12.5px">New <span class="accent">features</span> that are no less cool that you have to try</h2>
  <p class="abs tiny" style="left:6px;top:125px;width:146px;text-align:center;font-size:5.4px">The new features are more sophisticated than the previous features and contain many advanced technologies in processing</p>

  <div class="card" style="top:192px;height:138px"><div class="ico"></div><h4>AI Instant Website Generator</h4>
    <ul><li>Get a polished, SEO-ready website in seconds.</li><li>Includes custom domain, secure hosting, pro images.</li></ul><div class="btn">Read more</div></div>
  <div class="card" style="top:354px;height:138px"><div class="ico"></div><h4 style="margin-top:6px">AI Chatbot</h4>
    <ul><li>Fully trainable chatbot that learns your business.</li><li>Built-in CRM features for leads and contact forms.</li></ul><div class="btn" style="margin-top:6px">Read more</div></div>
  <div class="card" style="top:516px;height:138px"><div class="ico"></div><h4>Online Store Builder with AI Assistance</h4>
    <ul><li>Sell your products online and sync inventory.</li><li>Accept payments from many gateways including cards.</li></ul><div class="btn">Read more</div></div>
  <div class="card" style="top:678px;height:90px"><div class="ico"></div><h4>AI Auto-Blogging System</h4>
    <ul><li>Auto-publish fresh articles on your blog.</li></ul></div>
</section>

<!-- advantage + resources -->
<section class="col col-4">
  <div class="abs" style="left:0;top:0;width:158px;height:355px;background:var(--navy)"></div>
  <div class="media" role="img" aria-label="Video still of a robot head" style="left:14px;top:18px;width:128px;height:79px;border-radius:0;background:linear-gradient(135deg,#2d7f96,#173f5d 60%,#0c2039)"></div>
  <svg class="abs" style="left:67px;top:46px" width="22" height="22" viewBox="0 0 22 22"><circle cx="11" cy="11" r="11" fill="#1b74dc"/><path d="M8.5 6.5v9l7-4.5z" fill="#fff"/></svg>
  <h2 class="abs h" style="left:17px;top:136px;font-size:12.5px;color:#fff;font-weight:400">The AI Advantage in Website Building</h2>
  <p class="abs" style="left:20px;top:183px;width:120px;font-size:5.6px;line-height:1.3;color:#dce7f7">The last decade has seen AI grow from performing basic tasks to solving complex challenges, becoming a staple in our daily lives.</p>
  <div class="btn" style="left:44px;top:257px;width:57px;height:19px;font-size:6.5px">Explore</div>
  <div class="abs" style="left:46px;top:297px;display:flex;align-items:center;gap:4px;color:#fff;font-size:6.5px">
    <svg width="8" height="8" viewBox="0 0 8 8"><circle cx="4" cy="4" r="3.5" fill="none" stroke="#fff" stroke-width=".8"/><path d="M3.2 2.5v3l2.2-1.5z" fill="#fff"/></svg>How it work</div>

  <div class="tag" style="left:54px;top:408px;width:50px;font-size:5.5px;padding:3px 2px">Other Feature</div>
  <div class="abs" style="left:0;top:425px;width:12px;height:20px;background:#d6ebfa"></div>
  <h2 class="abs h" style="left:4px;top:436px;width:150px;text-align:center;font-size:12.5px">Additional <span class="accent">Resources</span> to Help Launch Your Business</h2>
  <p class="abs tiny" style="left:10px;top:502px;width:138px;text-align:center;font-size:5.4px">The new features are more sophisticated than the previous features and contain many advanced technologies in processing</p>
  <svg class="abs" style="left:0;top:552px" width="158" height="180" viewBox="0 0 158 180">
    <ellipse cx="79" cy="90" rx="65" ry="85" fill="none" stroke="#1b74dc" stroke-width=".7" stroke-dasharray="2 2"/>
    <ellipse cx="79" cy="90" rx="18" ry="26" fill="none" stroke="#1b74dc" stroke-width=".7" stroke-dasharray="2 2"/>
    <circle cx="79" cy="90" r="11" fill="#0d2a57"/><circle cx="79" cy="90" r="6" fill="#1ba6e8"/>
  </svg>
  <span class="chip" style="left:32px;top:588px">Bulk AI Content</span>
  <span class="chip" style="left:86px;top:589px">Get Your LLC</span>
  <span class="chip" style="left:12px;top:614px">Print Services</span>
  <span class="chip" style="left:103px;top:614px">Website Design</span>
  <span class="chip" style="left:12px;top:645px">Patent App</span>
  <span class="chip" style="left:106px;top:645px">Search Ads</span>
  <span class="chip" style="left:22px;top:675px">Trademark Reg</span>
  <span class="chip" style="left:94px;top:675px">Social Media</span>
  <span class="chip" style="left:56px;top:708px">Logo Design</span>
</section>

<!-- testimonials + cta -->
<section class="col col-5">
  <div class="abs" style="left:0;top:0;width:158px;height:12px;background:#fff"></div>
  <div class="abs" style="left:0;top:31px;width:16px;height:20px;background:#d6ebfa"></div>
  <h2 class="abs h" style="left:14px;top:42px;font-size:12.5px">What Our<br>Site <span class="accent">Owners Says</span></h2>
  <p class="abs tiny" style="left:17px;top:92px;font-size:6px">Their response after using our services</p>
  <div class="review" style="top:132px">
    <div class="stars">★★★★★<span>4.9</span></div>
    <p>"The website is an excellent example of how thoughtful design can enhance user experience. From the moment you land on the homepage"</p>
    <div class="who"><i></i><div><b>Maren Olvik</b><small>CEO of studio</small></div></div>
  </div>
  <div class="review" style="top:252px">
    <div class="stars">★★★★★<span>4.9</span></div>
    <p>"The website is an excellent example of how thoughtful design can enhance user experience. From the moment you land on the homepage"</p>
    <div class="who"><i></i><div><b>Maren Olvik</b><small>CEO of studio</small></div></div>
  </div>
  <svg class="abs" style="left:55px;top:382px" width="55" height="22" viewBox="0 0 55 22">
    <circle cx="11" cy="11" r="10" fill="none" stroke="#1d2b3f" stroke-width=".8"/><path d="M16 11H6m4-4-4 4 4 4" fill="none" stroke="#1d2b3f" stroke-width=".8"/>
    <circle cx="43" cy="11" r="10" fill="none" stroke="#1d2b3f" stroke-width=".8"/><path d="M38 11h10m-4-4 4 4-4 4" fill="none" stroke="#1d2b3f" stroke-width=".8"/>
  </svg>
  <div class="abs" style="left:18px;top:456px;width:125px;height:300px;background:var(--navy);border-radius:5px;overflow:hidden">
    <div class="media" role="img" aria-label="Robotic hand holding a glowing emblem" style="left:0;top:10px;width:125px;height:95px;border-radius:0;background:radial-gradient(ellipse at 60% 30%,#2a7fd0,#1d3d7a 50%,#0d2a57)"></div>
    <h3 class="abs h" style="left:16px;top:113px;font-size:12.5px;color:#fff;font-weight:400">Let's try for free now!</h3>
    <p class="abs" style="left:16px;top:162px;width:88px;font-size:5.6px;line-height:1.3;color:#dce7f7">Harness the power of AI and embark on your website creation journey with Pavlora. Whether you're looking to launch a new business, showcase your portfolio, or start a blog, Pavlora is your go-to AI Website Builder, ready to bring your digital vision to life.</p>
    <div class="btn" style="left:20px;top:264px;width:84px;height:20px;background:var(--btn-light);font-size:7px">Build free website</div>
  </div>
</section>

<!-- footer -->
<section class="col col-6 foot">
  <div class="abs" style="left:0;top:0;width:158px;height:198px;background:#fff"></div>
  <div class="abs" style="left:18px;top:0;width:125px;height:176px;background:var(--navy);border-radius:0 0 6px 6px"></div>
  <p class="abs" style="left:34px;top:18px;width:82px;font-size:5.6px;line-height:1.3;color:#dce7f7">Harness the power of AI and embark on your website creation journey with Pavlora. Whether you're looking to launch a new business, showcase your portfolio, or start a blog, Pavlora is your go-to AI Website Builder, ready to bring your digital vision to life.</p>
  <div class="btn" style="left:38px;top:121px;width:84px;height:21px;background:var(--btn-light);font-size:7px">Build free website</div>

  <div class="brand" style="left:20px;top:225px;font-size:10.5px;gap:6px"><span class="dot" style="width:17px;height:17px"></span>Pavlora</div>
  <p class="abs" style="left:32px;top:257px;width:112px;font-size:5.6px;line-height:1.9;color:#fff">It'll take minutes or less! Just answer a few basic questions and watch your stunning new website generate in seconds!</p>
  <h5 style="top:324px">Navigation</h5>
  <a style="top:353px">About Us</a><a style="top:371px">Features</a><a style="top:388px">Pricing</a><a style="top:406px">Blog</a>
  <h5 style="top:447px">Contact Us</h5>
  <a style="top:476px;left:36px">Contact us</a><a style="top:494px;left:36px">Privacy Policy</a><a style="top:511px;left:36px">Term of Service</a><a style="top:529px;left:36px">Disclaimer</a>
  <h5 style="top:569px;left:36px">Newsletter</h5>
  <p class="abs" style="left:38px;top:597px;width:118px;font-size:6.5px;line-height:1.5;color:#fff">Lorem ipsum dolor sit amet, consectetur adipiscing elit. Sed do eiusmod tempor .</p>
  <div class="abs" style="left:38px;top:635px;width:80px;height:17px;background:#fff;font-size:4px;color:#9aa6b8;padding:6px 7px">Your Email Address</div>
  <div class="btn" style="left:118px;top:635px;width:33px;height:17px;background:var(--btn-light);font-size:6.5px;border-radius:0">Send</div>
  <div class="abs" style="left:40px;top:709px;display:flex;gap:6px;font-size:5px;color:#fff">
    <span>Snapla</span><span>Worklinq</span><span>Facio</span><span>Chirpo</span>
  </div>
  <div class="abs" style="left:32px;top:745px;width:110px;height:1px;background:#5a7099"></div>
</section>

</body>
</html>
```